Bright Nook Home Page (A Home Wellness e-commerce site & blog)

We need a dynamic home page created for a home wellness brand. Must be visually appealing and extremely mobile-friendly. Logos and a Navmap have been provided but that is just a guideline, PLEASE USE YOUR CREATIVITY.

Target Market(s)

1st target demo: females 24-48, 2nd target demo: all 24-48

Number of Pages Required

1 page

```html
<!DOCTYPE html>
<html lang="en">
<head>
<meta charset="utf-8">
<title>Bright Nook — Home Wellness</title>
<link rel="stylesheet" href="https://fonts.googleapis.com/css2?family=Roboto:wght@300;400;500;700&family=Arimo:wght@400;700&display=swap">
<style>
  :root {
    --purple: #3d1a78;
    --purple-deep: #351568;
    --teal: #2fb3bd;
    --ink: #111111;
    --body: #4a4a4a;
    --mist: #f2f1f1;
    --white: #ffffff;
  }
  * { box-sizing: border-box; margin: 0; padding: 0; }
  html, body { width: 1200px; height: 3498px; overflow: hidden; }
  body { font-family: "Roboto", sans-serif; color: var(--ink); background: var(--white); position: relative; }
  .abs { position: absolute; }

  .promo-strip { top: 0; left: 0; width: 1200px; height: 46px; background: var(--teal); color: var(--white); font-size: 15px; display: flex; align-items: center; justify-content: center; }
  .site-nav { top: 46px; left: 0; width: 1200px; height: 74px; background: var(--purple); }
  .brand { left: 145px; top: 16px; color: var(--white); font-size: 36px; font-weight: 500; letter-spacing: -0.5px; display: flex; align-items: center; gap: 10px; }
  .brand-dot { width: 14px; height: 14px; border-radius: 50%; background: var(--teal); }
  .menu { left: 540px; top: 24px; display: flex; gap: 24px; font-size: 12.5px; color: var(--white); }
  .menu span { padding-bottom: 6px; }
  .menu .active { border-bottom: 2px solid var(--teal); }
  .nav-icon { top: 28px; }
  .social-mini { left: 900px; top: 31px; display: flex; gap: 12px; }
  .social-mini i { width: 12px; height: 12px; border-radius: 50%; background: var(--white); display: block; }
  .cart-count { left: 1036px; top: 14px; width: 18px; height: 18px; border-radius: 50%; background: var(--teal); color: var(--white); font-size: 10px; display: flex; align-items: center; justify-content: center; }

  .hero { top: 120px; left: 0; width: 1200px; height: 570px; background: linear-gradient(90deg, #e9e9ec 0%, #eeeef1 50%, #f2f2f3 100%); }
  .hero-portrait { left: 0; top: 0; width: 600px; height: 570px; background: radial-gradient(ellipse at 40% 55%, #b5785a 0%, #9a6247 40%, #e7e4e6 75%); }
  .hero-soap { left: 960px; top: 0; width: 240px; height: 165px; background: radial-gradient(ellipse at 60% 50%, #e6dca8 0%, #cdd2b4 45%, rgba(238,238,241,0) 75%); }
  .hero-butter { left: 950px; top: 370px; width: 250px; height: 200px; background: radial-gradient(ellipse at 50% 50%, #f2ead7 0%, #d9d2c2 40%, #6b4a3a 60%, rgba(238,238,241,0) 78%); }
  .hero-title { left: 595px; top: 178px; font-size: 82px; line-height: 1; color: var(--ink); }
  .hero-title b { font-weight: 700; } .hero-title span { font-weight: 300; }
  .hero-sub { left: 599px; top: 298px; font-size: 21px; color: #222; }
  .btn { background: var(--teal); color: var(--white); border-radius: 30px; font-weight: 500; display: flex; align-items: center; justify-content: center; text-transform: uppercase; }
  .hero-btn { left: 600px; top: 359px; width: 167px; height: 60px; font-size: 18px; }
  .dots { left: 626px; top: 491px; display: flex; gap: 12px; }
  .dots i { width: 8px; height: 8px; border-radius: 50%; background: #aaa; display: block; }
  .dots i.on { background: var(--purple); }

  .band { left: 0; width: 1200px; background: var(--purple); color: var(--white); }
  .sale-band { top: 690px; height: 84px; font-size: 27px; font-weight: 500; display: flex; align-items: center; justify-content: center; }
  .wave { left: 0; width: 1200px; }

  .section-title { left: 0; width: 1200px; text-align: center; font-size: 53px; line-height: 1; }
  .section-title b { font-weight: 700; } .section-title span { font-weight: 300; }
  .section-title .tint { color: var(--purple); }

  .tile { position: absolute; }

  .about { top: 1874px; left: 0; width: 1200px; height: 505px; background: var(--mist); }
  .about-still { left: 760px; top: 0; width: 440px; height: 505px; background: radial-gradient(circle at 55% 20%, #fbf6ea 0%, #e6e0d4 25%, rgba(242,241,241,0) 45%), radial-gradient(circle at 40% 60%, #ffffff 0%, #dedede 20%, rgba(242,241,241,0) 35%), radial-gradient(circle at 75% 55%, #5d7d3a 0%, rgba(242,241,241,0) 40%), radial-gradient(circle at 30% 85%, #d79a2e 0%, rgba(242,241,241,0) 25%), #eeedeb; }
  .about-title { left: 145px; top: 80px; font-size: 53px; line-height: 58px; }
  .about-title b { font-weight: 700; display: block; }
  .about-title .tint { color: var(--purple); }
  .about-title .tint b { display: inline; } .about-title .tint span { font-weight: 300; }
  .about-copy { left: 145px; top: 220px; width: 588px; font-family: "Arimo", sans-serif; font-size: 14.5px; line-height: 29px; color: var(--body); }
  .about-btn { left: 145px; top: 364px; width: 215px; height: 60px; font-size: 19px; }

  .paylater-band { top: 2379px; height: 84px; }
  .paylater-text { left: 260px; top: 24px; font-size: 28px; font-weight: 500; }
  .paylater-brand { left: 752px; top: 18px; display: flex; align-items: center; gap: 12px; font-size: 42px; font-weight: 500; }
  .paylater-brand i { width: 44px; height: 44px; border-radius: 50%; background: var(--white); display: block; }

  .blog-sub { left: 0; top: 2657px; width: 1200px; text-align: center; font-size: 16px; color: #222; }
  .card { top: 2718px; width: 288px; height: 390px; }
  .card-photo { left: 0; top: 0; width: 288px; height: 209px; }
  .card-body { left: 13px; top: 177px; width: 262px; height: 213px; background: var(--white); padding: 26px 0 0 27px; }
  .card-body h3 { font-family: "Arimo", sans-serif; font-size: 17.5px; font-weight: 400; line-height: 21px; color: #111; }
  .card-body p { font-family: "Arimo", sans-serif; font-size: 12px; line-height: 21px; color: #666; margin-top: 12px; width: 236px; }
  .card-btn { left: 40px; top: 337px; width: 119px; height: 44px; font-size: 13px; }

  .footer { left: 0; top: 3160px; width: 1200px; height: 338px; }
  .footer-brand { left: 172px; top: 3245px; color: var(--white); font-size: 56px; font-weight: 500; display: flex; align-items: center; gap: 14px; }
  .footer-brand i { width: 20px; height: 20px; border-radius: 50%; background: var(--teal); display: block; }
  .footer-social { left: 250px; top: 3356px; display: flex; gap: 46px; }
  .footer-social i { width: 28px; height: 28px; border-radius: 50%; background: var(--white); display: block; }
  .newsletter-title { left: 613px; top: 3254px; color: var(--white); font-size: 24px; font-weight: 500; }
  .newsletter { left: 615px; top: 3314px; width: 414px; height: 55px; background: var(--white); border-radius: 30px; }
  .newsletter span { position: absolute; left: 33px; top: 19px; font-family: "Arimo", sans-serif; font-size: 12px; color: #666; }
  .newsletter-btn { position: absolute; left: 274px; top: 5px; width: 135px; height: 45px; font-size: 19px; }
  .chat-bubble { left: 1137px; top: 3386px; width: 34px; height: 34px; border-radius: 50%; background: var(--teal); }
  .legal { left: 0; top: 3447px; width: 1200px; text-align: center; color: var(--white); font-size: 12px; }
</style>
</head>
<body>

  <div class="abs promo-strip">Free shipping on all orders $50 and over!</div>

  <header class="abs site-nav">
    <div class="abs brand"><i class="brand-dot"></i>Bright Nook</div>
    <nav class="abs menu">
      <span class="active">HOME</span><span>PRODUCTS</span><span>ABOUT US</span><span>BLOG</span>
    </nav>
    <svg class="abs nav-icon" style="left:840px" width="14" height="14" viewBox="0 0 14 14" aria-label="Search">
      <circle cx="6" cy="6" r="4.2" fill="none" stroke="#fff" stroke-width="2"/><line x1="9" y1="9" x2="13" y2="13" stroke="#fff" stroke-width="2.2"/>
    </svg>
    <div class="abs social-mini" aria-label="Social links"><i></i><i></i><i></i></div>
    <svg class="abs" style="left:1018px;top:24px" width="28" height="24" viewBox="0 0 28 24" aria-label="Cart">
      <path d="M1 2h5l3 13h14l3-9H8" fill="none" stroke="#fff" stroke-width="2.5" stroke-linejoin="round"/>
      <path d="M9 6h17l-3 9H10z" fill="#fff"/>
      <circle cx="11" cy="20" r="2.3" fill="#fff"/><circle cx="21" cy="20" r="2.3" fill="#fff"/>
    </svg>
    <div class="abs cart-count">0</div>
  </header>

  <section class="abs hero">
    <div class="abs hero-portrait" role="img" aria-label="Smiling woman holding a jar of face cream on her open palm"></div>
    <div class="abs hero-soap" role="img" aria-label="Bars of handmade soap tied with twine and olive leaves"></div>
    <div class="abs hero-butter" role="img" aria-label="Glass bowl of shea butter with shea nuts"></div>
    <h1 class="abs hero-title"><b>Bright</b><span>Nook</span></h1>
    <p class="abs hero-sub">Lorem ipsum dolor sit amet consectetur</p>
    <div class="abs btn hero-btn">Shop now</div>
    <div class="abs dots"><i></i><i class="on"></i><i></i></div>
  </section>

  <div class="abs band sale-band">50% off sale going on now! Because saving money also makes us happy</div>
  <svg class="abs wave" style="top:770px" width="1200" height="50" viewBox="0 0 1200 50" preserveAspectRatio="none">
    <path d="M0 4 Q600 70 1200 4 V0 H0Z" fill="#2fb3bd"/>
    <path d="M0 0 Q600 58 1200 0 V0 H0Z" fill="#3d1a78"/>
    <rect x="0" y="0" width="1200" height="4" fill="#3d1a78"/>
  </svg>

  <h2 class="abs section-title" style="top:900px"><b>Featured</b> <span>Products</span></h2>

  <div class="tile" style="left:153px;top:1007px;width:292px;height:236px;background:linear-gradient(180deg,#9cc764 0%,#c6dc8e 55%,#8a3c1c 100%)" role="img" aria-label="Drop of oil falling from a leaf into an amber bottle"></div>
  <div class="tile" style="left:153px;top:1251px;width:292px;height:284px;background:linear-gradient(160deg,#e6e6e8 0%,#b79b86 45%,#5a3a2a 70%,#d9d9dc 100%)" role="img" aria-label="Handmade soap bars in a wicker tray"></div>
  <div class="tile" style="left:153px;top:1543px;width:292px;height:261px;background:linear-gradient(120deg,#c9a98e 0%,#8e6e58 45%,#e8e2dc 100%)" role="img" aria-label="Smiling woman in a bathrobe holding a cream jar"></div>
  <div class="tile" style="left:453px;top:1007px;width:293px;height:259px;background:linear-gradient(180deg,#6f8fa0 0%,#7e5a44 45%,#9db0ba 100%)" role="img" aria-label="Laughing woman wearing a coffee face scrub"></div>
  <div class="tile" style="left:453px;top:1274px;width:293px;height:261px;background:radial-gradient(circle at 50% 50%,#f4f4f4 0%,#ebebeb 45%,#8aa872 80%,#d8c39a 100%)" role="img" aria-label="Flat lay of skincare jars, leaves and soap"></div>
  <div class="tile" style="left:453px;top:1543px;width:293px;height:261px;background:linear-gradient(180deg,#d9d4c4 0%,#c28a2e 45%,#e0c23a 70%,#4f7a3a 100%)" role="img" aria-label="Glass bottles of essential oils with cork stoppers"></div>
  <div class="tile" style="left:755px;top:1007px;width:293px;height:544px;background:linear-gradient(180deg,#dedad5 0%,#efefef 30%,#e8e2de 55%,#3f7a2e 70%,#c9a796 100%)" role="img" aria-label="Woman in a towel wrap with a clay face mask holding a leaf"></div>
  <div class="tile" style="left:755px;top:1559px;width:293px;height:245px;background:radial-gradient(circle at 50% 55%,#a8703c 0%,#d9b98a 30%,#ececec 65%)" role="img" aria-label="Flat lay of soap dish, bath brush and spa stones"></div>

  <section class="abs about">
    <div class="abs about-still" role="img" aria-label="Candle, cream jars, honey dipper and green leaves"></div>
    <h2 class="abs about-title"><b>About</b><span class="tint"><b>Bright</b><span>Nook</span></span></h2>
    <p class="abs about-copy">They say that home is where the heart is. But home is also where your mind and body reside. At Bright Nook we believe that home should be your place of Zen. A respite from the crazy world outside those walls. It is where you recharge your soul so you can approach each day with the focus and energy necessary to conquer the world.</p>
    <div class="abs btn about-btn">Tell me more</div>
  </section>

  <div class="abs band paylater-band">
    <div class="abs paylater-text">Don’t sweat it. You can pay later.</div>
    <div class="abs paylater-brand"><i></i>Settlebee</div>
  </div>
  <svg class="abs wave" style="top:2459px" width="1200" height="50" viewBox="0 0 1200 50" preserveAspectRatio="none">
    <path d="M0 4 Q600 70 1200 4 V0 H0Z" fill="#2fb3bd"/>
    <path d="M0 0 Q600 58 1200 0 V0 H0Z" fill="#3d1a78"/>
    <rect x="0" y="0" width="1200" height="4" fill="#3d1a78"/>
  </svg>

  <h2 class="abs section-title" style="top:2580px"><b>The</b> <b class="tint">Bright</b> <span class="tint">Blog</span></h2>
  <p class="abs blog-sub">Food for the mind, tips for the body and exercises for the soul</p>

  <article class="abs card" style="left:144px">
    <div class="abs card-photo" style="background:radial-gradient(circle at 60% 40%,#f3efe9 0%,#b89a72 35%,#5d7a4a 70%,#e9e9e9 100%)" role="img" aria-label="Spa flat lay with candle and succulent on a woven mat"></div>
    <div class="abs card-body"><h3>Lorem ipsum dolor smet consectetur</h3><p>Lorem ipsum dolor sit amet, consectetur adipiscing elit, sed do eiusmod tempor incididunt ut labore et dolore magna</p></div>
    <div class="abs btn card-btn">Read more</div>
  </article>
  <article class="abs card" style="left:456px">
    <div class="abs card-photo" style="background:radial-gradient(circle at 50% 50%,#e8d2c6 0%,#ededed 45%,#dcdcdc 100%)" role="img" aria-label="Hands holding a white cosmetic bottle"></div>
    <div class="abs card-body"><h3>Lorem ipsum dolor smet consectetur</h3><p>Lorem ipsum dolor sit amet, consectetur adipiscing elit, sed do eiusmod tempor incididunt ut labore et dolore magna</p></div>
    <div class="abs btn card-btn">Read more</div>
  </article>
  <article class="abs card" style="left:768px">
    <div class="abs card-photo" style="background:radial-gradient(circle at 50% 50%,#f2f2f2 0%,#e2e2e2 40%,#4f7a33 80%,#c9a24a 100%)" role="img" aria-label="Skincare tubes and spoons among fern leaves"></div>
    <div class="abs card-body"><h3>Lorem ipsum dolor smet consectetur</h3><p>Lorem ipsum dolor sit amet, consectetur adipiscing elit, sed do eiusmod tempor incididunt ut labore et dolore magna</p></div>
    <div class="abs btn card-btn">Read more</div>
  </article>

  <svg class="abs footer" width="1200" height="338" viewBox="0 0 1200 338" preserveAspectRatio="none">
    <path d="M0 53 Q600 -40 1200 53 V338 H0Z" fill="#2fb3bd"/>
    <path d="M0 60 Q600 -28 1200 60 V338 H0Z" fill="#3d1a78"/>
  </svg>
  <div class="abs footer-brand"><i></i>Bright Nook</div>
  <div class="abs footer-social" aria-label="Social links"><i></i><i></i><i></i></div>
  <h3 class="abs newsletter-title">Newsletter Sign up</h3>
  <div class="abs newsletter"><span>Enter Email</span><div class="btn newsletter-btn">Submit</div></div>
  <div class="abs chat-bubble" aria-label="Chat"></div>
  <p class="abs legal">© 2021 Bright Nook. All rights reserved &nbsp;| Terms &amp; Conditions &nbsp;| &nbsp;Privacy Policy</p>

</body>
</html>
```